Harbor Ridge Painting Epoxy Flyer

We need a promotional flyer for a new epoxy floor coatings division of our painting company. We do epoxy garage floor coatings and paver sealing. It needs to be based on and very similar to the attached flyer. The garage floor picture needs to look more realistic, and the before and after pavers pictures should look less shiny but still a good contrast. Include attached logo

```html
<!DOCTYPE html>
<html lang="en">
<head>
<meta charset="utf-8">
<title>Harbor Ridge Painting – Epoxy Flyer</title>
<link rel="stylesheet" href="https://fonts.googleapis.com/css2?family=Oswald:wght@500;600;700&family=Poppins:wght@500;600&display=swap">
<style>
  :root {
    --backdrop: #c2c2c2;
    --ink: #000000;
    --paper: #ffffff;
    --blue: #1e88e5;
    --green: #4ea81f;
    --orange: #d8740e;
    --teal: #1d9c9a;
    --text-dark: #0b0b0b;
  }
  * { margin: 0; padding: 0; box-sizing: border-box; }
  html, body { width: 904px; height: 1200px; overflow: hidden; background: var(--backdrop); }

  .flyer {
    position: absolute; left: 137px; top: 127px;
    width: 1162px; height: 1743px;
    transform: scale(0.5426); transform-origin: 0 0;
    background: var(--ink); color: var(--paper);
    font-family: "Poppins", sans-serif;
    overflow: hidden;
  }
  .abs { position: absolute; }

  /* hero */
  .hero-art { position: absolute; left: 0; top: 0; width: 1162px; height: 640px; }

  .brand { left: 70px; top: 155px; width: 380px; display: flex; align-items: center; gap: 18px; }
  .brand-dot { width: 64px; height: 64px; border-radius: 50%; background: var(--teal); flex: none; }
  .brand-name { font-family: "Poppins", sans-serif; font-weight: 600; font-size: 30px; line-height: 1.15; color: var(--paper); letter-spacing: 0.5px; }

  .headline { left: 53px; top: 345px; font-family: "Oswald", sans-serif; font-weight: 700; line-height: 1; }
  .headline .line-1 { font-size: 98px; display: block; letter-spacing: -0.5px; }
  .headline .line-2 { font-size: 70px; display: block; letter-spacing: -0.3px; }
  .headline-sub { left: 55px; top: 519px; font-weight: 600; font-size: 33px; letter-spacing: 0.5px; }

  /* photo frames */
  .photo { position: absolute; overflow: hidden; }
  .tab {
    position: absolute; left: 0; width: 50px; height: 128px;
    border-radius: 0 26px 26px 0;
    display: flex; align-items: center; justify-content: center;
  }
  .tab span {
    transform: rotate(-90deg); white-space: nowrap;
    font-family: "Oswald", sans-serif; font-weight: 700; font-size: 30px; color: var(--paper);
  }
  .tab-blue { background: var(--blue); }
  .tab-green { background: var(--green); }

  .epoxy-before { left: 65px; top: 596px; width: 420px; height: 204px; border-radius: 34px 34px 0 0;
    background: linear-gradient(180deg, #cfcabc 0%, #b9b6ac 40%, #a6a8a3 60%, #8f938f 100%); }
  .epoxy-after { left: 65px; top: 815px; width: 420px; height: 204px; border-radius: 0 0 34px 34px;
    background: linear-gradient(180deg, #d6d2c6 0%, #c2beb3 40%, #9c9896 60%, #7f7b7b 100%); }

  .paver-before { left: 672px; top: 947px; width: 421px; height: 205px; border-radius: 34px 34px 0 0;
    background: linear-gradient(180deg, #4d6a35 0%, #6b7a55 22%, #918b80 45%, #857f77 100%); }
  .paver-after { left: 672px; top: 1166px; width: 421px; height: 204px; border-radius: 0 0 34px 34px;
    background: linear-gradient(180deg, #3f6a2a 0%, #4e5a3e 22%, #45464a 45%, #2f3034 100%); }

  /* service panels */
  .panel {
    position: absolute; border-radius: 20px; border: 3px solid var(--orange);
    border-top-color: var(--blue);
  }
  .pill {
    position: absolute; height: 50px; border-radius: 25px;
    display: flex; align-items: center; justify-content: center;
    font-family: "Oswald", sans-serif; font-weight: 700; font-size: 38px; color: var(--paper);
  }
  .pill-blue { background: var(--blue); }
  .pill-green { background: var(--green); }
  .checklist { position: absolute; list-style: none; font-size: 21.5px; font-weight: 500; line-height: 1.22; }
  .checklist li { position: relative; padding-left: 28px; margin-bottom: 17px; }
  .checklist li::before {
    content: ""; position: absolute; left: 0; top: 6px; width: 17px; height: 17px; border-radius: 50%;
    background: var(--tick, var(--blue));
  }
  .checklist li::after {
    content: ""; position: absolute; left: 5px; top: 9px; width: 4px; height: 8px;
    border: solid var(--paper); border-width: 0 2px 2px 0; transform: rotate(45deg);
  }
  .checklist.green { --tick: #56b52a; }

  .epoxy-panel { left: 516px; top: 653px; width: 429px; height: 253px; }
  .epoxy-pill { left: 545px; top: 631px; width: 371px; }
  .epoxy-list { left: 570px; top: 697px; width: 360px; }

  .paver-panel { left: 218px; top: 1088px; width: 429px; height: 251px; }
  .paver-pill { left: 247px; top: 1064px; width: 372px; }
  .paver-list { left: 243px; top: 1131px; width: 400px; }

  .tagline { left: 0; width: 1162px; top: 1396px; text-align: center;
    font-family: "Oswald", sans-serif; font-weight: 600; font-size: 38px; line-height: 1.3; }

  /* trust row */
  .trust { position: absolute; top: 1471px; display: flex; align-items: center; gap: 21px; }
  .trust-icon { width: 88px; height: 88px; flex: none; }
  .trust-text { font-family: "Oswald", sans-serif; font-weight: 600; font-size: 32px; line-height: 1.18; }
  .trust-licensed { left: 85px; }
  .trust-family { left: 390px; }
  .trust-area { left: 734px; }

  /* call band */
  .call-band { position: absolute; left: 0; top: 1589px; width: 1162px; height: 154px; background: var(--paper); color: var(--text-dark); }
  .call-label { position: absolute; left: 83px; top: 14px; font-family: "Oswald", sans-serif; font-weight: 700; line-height: 1; }
  .call-label .small { display: block; font-size: 46px; letter-spacing: -1px; }
  .call-label .big { display: block; font-size: 83px; margin-top: 1px; letter-spacing: -2px; }
  .phone-icon { position: absolute; left: 434px; top: 25px; width: 66px; height: 66px; }
  .phone-number { position: absolute; left: 518px; top: 18px; font-family: "Poppins", sans-serif; font-weight: 600; font-size: 80px; letter-spacing: -1px; line-height: 1.1; }
  .phone-note { position: absolute; left: 435px; top: 96px; font-weight: 500; font-size: 32px; }
</style>
</head>
<body>
<div class="flyer">

  <svg class="hero-art" viewBox="0 0 1162 640">
    <defs>
      <linearGradient id="swoosh" x1="0" y1="0" x2="0" y2="1">
        <stop offset="0" stop-color="#1a9aa0"/>
        <stop offset="0.4" stop-color="#2eaa4a"/>
        <stop offset="0.7" stop-color="#9a8a12"/>
        <stop offset="1" stop-color="#d8740e"/>
      </linearGradient>
      <linearGradient id="roomFloor" x1="0" y1="0" x2="0.6" y2="1">
        <stop offset="0" stop-color="#a7a39b"/>
        <stop offset="0.3" stop-color="#8d877f"/>
        <stop offset="0.75" stop-color="#776f67"/>
        <stop offset="1" stop-color="#8d7663"/>
      </linearGradient>
    </defs>
    <path d="M463 0 C500 330 770 615 1162 625 L1162 586 C748 546 538 286 513 0 Z" fill="url(#swoosh)"/>
    <path d="M513 0 C538 286 748 546 1162 586 L1162 0 Z" fill="url(#roomFloor)" stroke="#000" stroke-width="6" role="img" aria-label="Photo of a finished living room floor with wood-look coating beside a stone fireplace"/>
  </svg>

  <div class="abs brand">
    <span class="brand-dot"></span>
    <span class="brand-name">HARBOR RIDGE PAINTING</span>
  </div>

  <h1 class="abs headline">
    <span class="line-1">Upgrade Your</span>
    <span class="line-2">Garage &amp; Driveway</span>
  </h1>
  <p class="abs headline-sub">FROM WORN-OUT TO LIKE NEW</p>

  <div class="photo epoxy-before" role="img" aria-label="Garage floor before coating: bare grey concrete">
    <div class="tab tab-blue" style="top:0"><span>Before</span></div>
  </div>
  <div class="photo epoxy-after" role="img" aria-label="Garage floor after coating: speckled grey epoxy finish">
    <div class="tab tab-blue" style="top:0"><span>After</span></div>
  </div>

  <div class="panel epoxy-panel"></div>
  <div class="pill pill-blue epoxy-pill">Epoxy Floor Coatings</div>
  <ul class="checklist epoxy-list">
    <li>Durable, long-lasting finish</li>
    <li>Slip-resistant texture</li>
    <li>Covers cracks &amp;<br>imperfections</li>
    <li>Easy to clean &amp; maintain</li>
  </ul>

  <div class="photo paver-before" role="img" aria-label="Paver driveway before sealing: faded grey pavers with green lawn">
    <div class="tab tab-green" style="top:0"><span>Before</span></div>
  </div>
  <div class="photo paver-after" role="img" aria-label="Paver driveway after sealing: rich dark pavers with green lawn">
    <div class="tab tab-green" style="top:0"><span>After</span></div>
  </div>

  <div class="panel paver-panel"></div>
  <div class="pill pill-green paver-pill">Paver Sealing</div>
  <ul class="checklist green paver-list">
    <li>Restores color &amp; enhances<br>appearance</li>
    <li>Protects from sun fading</li>
    <li>Helps prevent weeds &amp; sand loss</li>
    <li>Easier to clean &amp; maintain</li>
  </ul>

  <p class="abs tagline">Practical upgrades that protect and improve your home</p>

  <div class="trust trust-licensed">
    <svg class="trust-icon" viewBox="0 0 88 88">
      <circle cx="44" cy="44" r="42" fill="#000" stroke="#2a7f7a" stroke-width="2"/>
      <path d="M30 52 L24 68 L32 64 L36 71 L40 58 M58 52 L64 68 L56 64 L52 71 L48 58" fill="#e0a11b"/>
      <circle cx="44" cy="40" r="20" fill="#1d9c9a"/>
      <path d="M34 40 L42 48 L56 31" fill="none" stroke="#7bd13a" stroke-width="6" stroke-linecap="round" stroke-linejoin="round"/>
    </svg>
    <p class="trust-text">Licensed &amp;<br>Insured</p>
  </div>
  <div class="trust trust-family">
    <svg class="trust-icon" viewBox="0 0 88 88">
      <circle cx="44" cy="44" r="42" fill="#000" stroke="#2a7f7a" stroke-width="2"/>
      <path d="M40 20 L58 26 V42 C58 54 50 62 40 66 C30 62 22 54 22 42 V26 Z" fill="#1d9c9a"/>
      <circle cx="40" cy="41" r="9" fill="none" stroke="#7bd13a" stroke-width="3"/>
      <path d="M36 41 L39 44 L44 38" fill="none" stroke="#7bd13a" stroke-width="3"/>
      <rect x="48" y="50" width="16" height="16" rx="3" fill="#e0a11b"/>
    </svg>
    <p class="trust-text">Family-Owned<br>Local Business</p>
  </div>
  <div class="trust trust-area">
    <svg class="trust-icon" viewBox="0 0 88 88">
      <circle cx="44" cy="44" r="42" fill="#000" stroke="#2a7f7a" stroke-width="2"/>
      <ellipse cx="44" cy="62" rx="20" ry="7" fill="none" stroke="#e0a11b" stroke-width="3"/>
      <path d="M44 62 C36 50 30 42 30 34 A14 14 0 0 1 58 34 C58 42 52 50 44 62 Z" fill="#3aa63a"/>
      <circle cx="44" cy="34" r="5" fill="#000"/>
    </svg>
    <p class="trust-text">Serving Cedar Bluff &amp;<br>Surrounding Areas</p>
  </div>

  <div class="call-band">
    <p class="call-label"><span class="small">CALL FOR A FREE</span><span class="big">ESTIMATE</span></p>
    <svg class="phone-icon" viewBox="0 0 68 68">
      <defs>
        <linearGradient id="phoneRing" x1="0" y1="1" x2="1" y2="0">
          <stop offset="0" stop-color="#d8740e"/>
          <stop offset="0.5" stop-color="#4ea81f"/>
          <stop offset="1" stop-color="#1e88e5"/>
        </linearGradient>
      </defs>
      <circle cx="34" cy="34" r="33" fill="url(#phoneRing)"/>
      <path d="M24 20 L30 19 L33 27 L29 30 C31 35 34 38 39 40 L42 36 L50 39 L49 45 C38 47 22 33 24 20 Z" fill="#fff"/>
    </svg>
    <p class="phone-number">555-204-0147</p>
    <p class="phone-note">Fast, professional service you can trust</p>
  </div>
</div>
</body>
</html>
```